Business Card for Fashion House

We need a business card design for our personalize fashion service for our customers. the business card should reflect reliability, luxury and creativity.
The brand Gravetto is extracted from "Graceful Velvetto"; Gravetto provides fashion designs sprinkled with luxury and style tailored for our elite clients character profile.
Gravetto is created for those who embody class and elegance with a passion for style.
Target Market(s)
Affluent Customers
Industry/Entity Type
Fashion
Contact Information for Business Card
Samira Haddadin
Fashion Designer
Telephone: +971 4 555 0192
Mobile +971 50 555 0147
Emal info@gravetto-example.com
Website www.gravetto-example.com
Social Media Youtube g+ Facebook Instagram Pin /gravetto
Font styles to use
Other font styles liked:
- Audrey provided
Look and feel
Each slider illustrates characteristics of the customer's brand and the style your logo design should communicate.

```html
<!DOCTYPE html>
<html lang="en">
<head>
<meta charset="utf-8">
<title>Gravetto Business Card</title>
<link href="https://fonts.googleapis.com/css2?family=Cinzel:wght@400&family=Cormorant+Garamond:wght@500&family=Roboto:wght@400&display=swap" rel="stylesheet">
<style>
  :root {
    --backdrop: #e4e4e4;
    --card-dark: #232524;
    --card-light: #ffffff;
    --ink: #1e1e1e;
    --ink-soft: #333333;
    --on-dark: #f4f4f4;
  }
  * { margin: 0; padding: 0; box-sizing: border-box; }
  html, body {
    width: 1200px; height: 852px; overflow: hidden;
    background: var(--backdrop);
  }
  .canvas { position: relative; width: 1200px; height: 852px; }

  .card {
    position: absolute; top: 276px;
    width: 525px; height: 300px;
    border-radius: 22px;
    overflow: hidden;
  }
  .card--front { left: 60px; background: var(--card-dark); }
  .card--back  { left: 615px; background: var(--card-light); }

  /* Front */
  .brand-name {
    position: absolute; left: 0; right: 0; top: 128px;
    text-align: center;
    font-family: "Cinzel", serif;
    font-weight: 400;
    font-size: 34px;
    letter-spacing: 14px;
    padding-left: 14px;
    color: var(--on-dark);
  }

  /* Back */
  .holder {
    position: absolute; left: 0; width: 525px; top: 42px;
    text-align: center;
  }
  .holder-name {
    font-family: "Cormorant Garamond", serif;
    font-weight: 500;
    font-size: 24px;
    color: var(--ink);
    line-height: 1;
  }
  .holder-title {
    font-family: "Roboto", sans-serif;
    font-size: 10px;
    color: var(--ink-soft);
    margin-top: 4px;
  }
  .rule {
    position: absolute; height: 1px; background: var(--ink);
  }
  .rule--top { left: 345px; right: 18px; top: 86px; }
  .rule--bottom { left: 22px; width: 280px; top: 262px; }

  .contact-icons {
    position: absolute; left: 0; width: 525px; top: 116px;
    display: flex; justify-content: center; gap: 6px;
  }
  .contact-icons svg { width: 12px; height: 12px; }
  .contact-list {
    position: absolute; left: 0; width: 525px; top: 136px;
    text-align: center;
    font-family: "Roboto", sans-serif;
    font-size: 13px;
    line-height: 15px;
    color: var(--ink);
    list-style: none;
  }
  .social {
    position: absolute; left: 0; width: 525px; top: 214px;
    display: flex; justify-content: center; align-items: center; gap: 6px;
    font-family: "Roboto", sans-serif;
    font-size: 13px;
    color: var(--ink);
  }
  .social-dot {
    width: 11px; height: 11px; border-radius: 50%;
    background: var(--ink);
  }
</style>
</head>
<body>
<main class="canvas">
  <section class="card card--front" aria-label="Card front">
    <h1 class="brand-name">GRAVETTO</h1>
  </section>

  <section class="card card--back" aria-label="Card back">
    <div class="holder">
      <h2 class="holder-name">Samira Haddadin</h2>
      <p class="holder-title">Fashion Designer</p>
    </div>
    <div class="rule rule--top"></div>

    <div class="contact-icons" aria-hidden="true">
      <svg viewBox="0 0 12 12"><circle cx="6" cy="6" r="5.3" fill="none" stroke="#1e1e1e" stroke-width="1"/><path d="M4 3.5l1 1.2-.6.7c.5 1 1.2 1.7 2.2 2.2l.7-.6 1.2 1-.7.9C5.6 8.7 3.3 6.4 3.1 4.2z" fill="#1e1e1e"/></svg>
      <svg viewBox="0 0 12 12"><rect x="3" y="0.8" width="6" height="10.4" rx="1.2" fill="none" stroke="#1e1e1e" stroke-width="1.1"/><rect x="4.2" y="2.2" width="3.6" height="6" fill="#1e1e1e"/></svg>
      <svg viewBox="0 0 12 12"><rect x="0.8" y="2.3" width="10.4" height="7.4" fill="none" stroke="#1e1e1e" stroke-width="1"/><path d="M0.8 2.5L6 6.6l5.2-4.1" fill="none" stroke="#1e1e1e" stroke-width="1"/></svg>
      <svg viewBox="0 0 12 12"><circle cx="6" cy="6" r="5.2" fill="none" stroke="#1e1e1e" stroke-width="1"/><ellipse cx="6" cy="6" rx="2.2" ry="5.2" fill="none" stroke="#1e1e1e" stroke-width="0.9"/><path d="M0.8 6h10.4M1.6 3.4h8.8M1.6 8.6h8.8" stroke="#1e1e1e" stroke-width="0.8"/></svg>
    </div>

    <ul class="contact-list">
      <li>+971 4 555 0192</li>
      <li>+971 50 555 0147</li>
      <li>info@gravetto-example.com</li>
      <li>www.gravetto-example.com</li>
    </ul>

    <div class="social">
      <span class="social-dot" aria-hidden="true"></span>
      <span>/gravetto</span>
    </div>
    <div class="rule rule--bottom"></div>
  </section>
</main>
</body>
</html>
```